Website for my law practice

I am a solo practitioner, who specializes in family law and estate planning in Massachusetts. I need to re-do my website, as it is outdated. I like the idea of a nontraditional law firm website. My website address is: doloresquintanalaw.com. I would like to retain my logo in the green color, as part of the new website. I have uploaded my logo below.

My hourly rate has changed from what is listed on my current website. My new hourly rate is $385.00. Please use this hourly rate when creating the website.

Good morning,

I have reviewed the designs submitted so far. I am happy that the "dq" logo in the green color is part of each of the designs submitted. I am also happy that the standard items seen in law firm websites, such as the scales of justice, etc. were not incorporated. Although the green logo is great, I do not think rest of the website has to have the same green color throughout. Additionally, I was hoping for something more creative, to make the website standout and not the stock web designs you see everyday. Please incorporate more unique images if you can. For example of what I mean, please look at this website: https://www.rosalindfenwicklaw.com

```html
<!DOCTYPE html>
<html lang="en">
<head>
<meta charset="utf-8">
<title>Dolores Quintana – Attorney at Law – Homepage Concepts</title>
<link href="https://fonts.googleapis.com/css2?family=Jost:wght@300;400;500;600&family=Roboto:wght@400;500;700&display=swap" rel="stylesheet">
<style>
:root{
  --green:#4a8a38;
  --green-dark:#3f7a2f;
  --green-pale:#eef4ec;
  --green-pale-2:#e6efdf;
  --ring:#e3ecdc;
  --ink:#222;
  --text:#444;
  --grey-card:#e4e4e4;
  --input-border:#e2e2e2;
  --footer-dark:#343434;
  --board:#bdbdbd;
  --white:#fff;
}
*{box-sizing:border-box;margin:0;padding:0}
html,body{width:1172px;height:1200px;overflow:hidden;background:var(--board)}
.board{position:absolute;left:0;top:0;width:1904px;height:1950px;transform:scale(.61555);transform-origin:0 0;background:var(--board)}
.page{position:absolute;top:103px;width:833px;height:1743px;background:var(--white);overflow:hidden;font-family:Roboto,sans-serif;color:var(--ink);box-shadow:0 10px 30px rgba(0,0,0,.18)}
.page--dark{left:87px}
.page--light{left:984px}
.abs{position:absolute}

/* header */
.site-header{position:absolute;left:0;top:0;width:833px;height:85px;border-top:4px solid var(--green);background:var(--white)}
.brand{position:absolute;left:77px;top:18px;display:flex;align-items:center;gap:10px}
.brand__mark{width:36px;height:36px;border-radius:50%;border:4px solid var(--green)}
.brand__name{font-family:Jost,sans-serif;font-weight:400;font-size:10.5px;line-height:12px;color:var(--green);letter-spacing:.3px}
.nav{position:absolute;left:269px;top:35px;display:flex;align-items:center;font-size:9.5px;font-weight:500;letter-spacing:.2px}
.nav a{color:var(--ink);text-decoration:none;margin-right:23px}
.nav a.is-active{background:var(--green);color:var(--white);border-radius:11px;padding:5px 13px;margin-right:11px}
.call{position:absolute;left:626px;top:29px;display:flex;align-items:center;gap:11px}
.call__icon{width:34px;height:34px;border-radius:50%;background:var(--white);box-shadow:0 2px 8px rgba(0,0,0,.15);display:flex;align-items:center;justify-content:center}
.call__label{font-size:7.5px;font-weight:500;line-height:9px}
.call__number{font-size:14px;font-weight:700;color:var(--green);letter-spacing:.4px}

/* hero */
.hero{position:absolute;left:0;top:85px;width:833px;height:400px;background:linear-gradient(180deg,#cfc9d2 0%,#d9d4d8 25%,#c7cfd4 48%,#a9b6bb 62%,#b8ad9c 80%,#a79780 100%)}
.hero__people{position:absolute;left:470px;top:20px;width:363px;height:370px;background:radial-gradient(ellipse at 60% 50%,#5a4032 0%,#7a5d4c 35%,rgba(150,130,115,.4) 65%,rgba(150,130,115,0) 80%)}
.hero__curve{position:absolute;left:0;top:0}
.hero__dots{position:absolute;left:37px;top:202px}
.hero__dots span{display:block;width:8px;height:8px;border-radius:50%;background:#aaa;margin-bottom:10px}
.hero__dots span.is-on{background:var(--green)}
.hero__title{position:absolute;left:77px;top:171px;font-family:Jost,sans-serif}
.hero__title h1{font-weight:500;font-size:30px;line-height:34px;color:var(--ink)}
.hero__title p{font-weight:300;font-size:30px;line-height:34px;color:var(--green)}
.rule{display:block;width:52px;height:3px;background:var(--green)}
.hero__rule{position:absolute;left:77px;top:239px}
.hero__text{position:absolute;left:77px;top:258px;width:400px;font-size:13.5px;line-height:20px;color:#111}
.btn{position:absolute;background:var(--green);color:var(--white);font-family:Roboto,sans-serif;font-weight:500;font-size:11px;border-radius:20px;display:flex;align-items:center;justify-content:center;letter-spacing:.2px}
.hero__btn{left:77px;top:315px;width:207px;height:33px}
.badge{position:absolute;left:388px;top:450px;width:56px;height:56px;border-radius:50%;background:var(--white);box-shadow:0 3px 10px rgba(0,0,0,.18);display:flex;align-items:center;justify-content:center;font-family:Jost,sans-serif;font-size:17px;font-weight:500;color:var(--green)}

/* about */
.portrait{position:absolute;left:77px;top:548px;width:310px;height:310px;border-radius:50%;border:7px solid var(--ring);background:var(--white);padding:5px}
.portrait__photo{width:100%;height:100%;border-radius:50%;background:radial-gradient(circle at 50% 40%,#9a9a9a 0%,#6f6f6f 45%,#3d3d3d 100%)}
.name-tag{position:absolute;left:233px;top:829px;width:157px;height:33px;border-radius:17px;background:var(--white);box-shadow:0 3px 10px rgba(0,0,0,.15);display:flex;align-items:center;gap:10px;padding-left:6px;font-family:Jost,sans-serif;font-size:11px;color:var(--ink)}
.name-tag__icon{width:22px;height:22px;border-radius:50%;background:var(--green);display:flex;align-items:center;justify-content:center}
.section-title{font-family:Jost,sans-serif;font-size:29px;line-height:34px;color:var(--ink);font-weight:600}
.section-title span{font-weight:300;color:var(--green)}
.about__title{position:absolute;left:416px;top:565px}
.about__rule{position:absolute;left:395px;top:602px;width:50px;height:3px}
.about__text{position:absolute;left:416px;top:626px;width:340px;font-size:11px;line-height:17.3px;color:var(--text);text-align:justify}
.about__text p{margin-bottom:9px}
.about__btn{left:416px;top:797px;width:106px;height:34px}

/* practice */
.centered{position:absolute;left:0;width:833px;text-align:center}
.practice__title{top:930px}
.practice__rule{position:absolute;left:391px;top:965px;width:52px;height:3px}
.card{position:absolute;top:998px;width:329px;height:106px;border-radius:8px;display:flex;align-items:center;justify-content:center;font-family:Jost,sans-serif;font-size:26px;font-weight:400}
.card--family{left:77px;background:var(--grey-card);color:var(--ink)}
.card--estate{left:426px;background:var(--green);color:var(--white)}

/* contact */
.contact{position:absolute;left:0;top:1169px;width:833px;height:309px}
.page--dark .contact{background:var(--green-pale)}
.page--light .contact{background:var(--green-pale-2)}
.contact__title{top:42px}
.contact__rule{position:absolute;left:391px;top:80px;width:52px;height:3px}
.field{position:absolute;background:var(--white);border:1px solid var(--input-border);box-shadow:0 2px 6px rgba(0,0,0,.05);font-size:10.5px;color:#333;padding:12px 12px}
.contact__btn{left:356px;top:228px;width:121px;height:31px;font-size:11.5px}

/* footer */
.footer{position:absolute;left:0;top:1478px;width:833px;height:265px}
.page--dark .footer{background:var(--footer-dark);color:var(--white)}
.page--light .footer{background:var(--white);color:var(--ink)}
.footer__brand{position:absolute;left:77px;top:96px;display:flex;align-items:center;gap:12px}
.footer__brand .brand__mark{width:48px;height:48px;border-width:5px}
.footer__brand .brand__name{font-size:14px;line-height:16px}
.footer__col{position:absolute;top:42px}
.footer__col h3{font-size:11px;font-weight:500;letter-spacing:.2px;padding-bottom:6px;border-bottom:3px solid var(--green);display:inline-block}
.footer__col ul{list-style:none;margin-top:23px}
.footer__col li{font-size:10px;line-height:26px}
.page--dark .footer__col li{color:#e6e6e6}
.footer__contact{position:absolute;left:574px;width:200px;display:flex;gap:10px;font-size:10px;line-height:16px}
.footer__contact b{font-weight:500}
.icon-circle{width:27px;height:27px;border-radius:50%;background:var(--white);flex:none;display:flex;align-items:center;justify-content:center;box-shadow:0 1px 5px rgba(0,0,0,.12)}
.footer__divider{position:absolute;left:77px;top:228px;width:678px;height:1px}
.page--dark .footer__divider{background:#5a5a5a}
.page--light .footer__divider{background:#ddd}
.footer__copy{position:absolute;left:0;top:240px;width:833px;text-align:center;font-size:9.5px}
.social{position:absolute;top:236px;left:676px;display:flex;gap:6px}
.social span{width:22px;height:22px;border-radius:50%;background:var(--white);box-shadow:0 1px 4px rgba(0,0,0,.15)}
.social span.is-hover{background:var(--green)}
</style>
</head>
<body>
<div class="board">

<!-- ============ Concept A: dark footer ============ -->
<section class="page page--dark">
  <header class="site-header">
    <div class="brand"><span class="brand__mark"></span><div class="brand__name">Dolores Quintana<br>Attorney at Law</div></div>
    <nav class="nav"><a class="is-active">HOME</a><a>ABOUT</a><a>SERVICES</a><a>LOCATION</a><a>FAQ</a><a>CONTACT</a></nav>
    <div class="call">
      <span class="call__icon"><svg width="14" height="14" viewBox="0 0 24 24"><path fill="#4a8a38" d="M6.6 10.8c1.4 2.8 3.8 5.1 6.6 6.6l2.2-2.2c.3-.3.7-.4 1-.2 1.1.4 2.3.6 3.6.6.6 0 1 .4 1 1V20c0 .6-.4 1-1 1C10.6 21 3 13.4 3 4c0-.6.4-1 1-1h3.5c.6 0 1 .4 1 1 0 1.3.2 2.5.6 3.6.1.3 0 .7-.2 1z"/></svg></span>
      <div><div class="call__label">CALL ME:</div><div class="call__number">617-555-0148</div></div>
    </div>
  </header>
  <div class="hero">
    <div class="hero__people" role="img" aria-label="Photo of a smiling family playing together on a beach at sunset"></div>
    <svg class="hero__curve" width="833" height="400" viewBox="0 0 833 400"><path d="M0 275 Q416 510 833 272 L833 400 L0 400Z" fill="#fff"/><path d="M0 275 Q416 510 833 272" fill="none" stroke="#4a8a38" stroke-width="4"/></svg>
  </div>
  <div class="hero__dots"><span></span><span class="is-on"></span><span></span><span></span></div>
  <div class="hero__title"><h1>Dolores Quintana</h1><p>Attorney At Law</p></div>
  <span class="rule hero__rule"></span>
  <p class="hero__text">Dolores Quintana is a Solo Practitioner focusing her practice on matters pertaining to family law and estate planning.</p>
  <div class="btn hero__btn">REQUEST A FREE CONSULTATION</div>
  <div class="badge">dq</div>

  <div class="portrait"><div class="portrait__photo" role="img" aria-label="Black and white portrait photo of the attorney"></div></div>
  <div class="name-tag"><span class="name-tag__icon"><svg width="10" height="10" viewBox="0 0 10 10"><circle cx="5" cy="3" r="2.2" fill="#fff"/><path d="M1 10c0-2.5 1.8-4 4-4s4 1.5 4 4z" fill="#fff"/></svg></span>Dolores Quintana</div>
  <h2 class="section-title about__title">About <span>Me</span></h2>
  <span class="rule about__rule"></span>
  <div class="about__text">
    <p>Dolores Quintana is a Solo Practitioner focusing her practice on matters pertaining to family law and estate planning.</p>
    <p>When I am retained, my clients are my priority. As a result, I work closely with each one to keep them informed through each step of the legal proceeding. Clients have always expressed to me how frustrating it is when attorneys don't return phone calls. I understand this, as I am often met with the same challenges in the profession. I am proud of my practice and my reputation, and I return calls promptly.</p>
  </div>
  <div class="btn about__btn">LEARN MORE</div>

  <h2 class="section-title centered practice__title">Practice <span>Areas</span></h2>
  <span class="rule practice__rule"></span>
  <div class="card card--family">Family Law</div>
  <div class="card card--estate">Estate Planning</div>

  <section class="contact">
    <h2 class="section-title centered contact__title">Get In <span>Touch</span></h2>
    <span class="rule contact__rule"></span>
    <div class="field" style="left:114px;top:107px;width:196px;height:34px">Full Name</div>
    <div class="field" style="left:318px;top:107px;width:196px;height:34px">Phone</div>
    <div class="field" style="left:521px;top:107px;width:196px;height:34px">Email Address</div>
    <div class="field" style="left:114px;top:151px;width:603px;height:64px">Message</div>
    <div class="btn contact__btn">SEND MESSAGE</div>
  </section>

  <footer class="footer">
    <div class="footer__brand"><span class="brand__mark"></span><div class="brand__name">Dolores Quintana<br>Attorney at Law</div></div>
    <div class="footer__col" style="left:304px"><h3>NAVIGATION</h3><ul><li>HOME</li><li>About Me</li><li>Services</li><li>Location</li><li>Contact Me</li></ul></div>
    <div class="footer__col" style="left:428px"><h3>QUICK LINKS</h3><ul><li>FAQ</li><li>Privacy Policy</li><li>Terms &amp; Conditions</li><li>Disclaimer</li></ul></div>
    <div class="footer__col" style="left:574px"><h3>CONTACT US</h3></div>
    <div class="footer__contact" style="top:88px"><span class="icon-circle"><svg width="9" height="11" viewBox="0 0 9 11"><path d="M4.5 0C2 0 0 2 0 4.4 0 7.5 4.5 11 4.5 11S9 7.5 9 4.4C9 2 7 0 4.5 0z" fill="#4a8a38"/><circle cx="4.5" cy="4.3" r="1.5" fill="#fff"/></svg></span><div>42 Harbor Lane Salem,<br>MA 01970</div></div>
    <div class="footer__contact" style="top:138px"><span class="icon-circle"><svg width="11" height="11" viewBox="0 0 24 24"><path fill="#4a8a38" d="M6.6 10.8c1.4 2.8 3.8 5.1 6.6 6.6l2.2-2.2c.3-.3.7-.4 1-.2 1.1.4 2.3.6 3.6.6.6 0 1 .4 1 1V20c0 .6-.4 1-1 1C10.6 21 3 13.4 3 4c0-.6.4-1 1-1h3.5c.6 0 1 .4 1 1 0 1.3.2 2.5.6 3.6.1.3 0 .7-.2 1z"/></svg></span><div><b>Call Me:</b><br>617-555-0148</div></div>
    <div class="footer__contact" style="top:188px"><span class="icon-circle"><svg width="11" height="8" viewBox="0 0 11 8"><rect width="11" height="8" rx="1" fill="#4a8a38"/><path d="M0.5 0.8 5.5 4.5 10.5 0.8" stroke="#fff" fill="none"/></svg></span><div><b>Email Me:</b><br>dolores.quintana@example.com</div></div>
    <div class="footer__divider"></div>
    <div class="footer__copy">© 2025 &nbsp;/&nbsp; All Rights Reserved</div>
    <div class="social"><span></span><span class="is-hover"></span><span></span></div>
  </footer>
</section>

<!-- ============ Concept B: light footer ============ -->
<section class="page page--light">
  <header class="site-header">
    <div class="brand"><span class="brand__mark"></span><div class="brand__name">Dolores Quintana<br>Attorney at Law</div></div>
    <nav class="nav"><a class="is-active">HOME</a><a>ABOUT</a><a>SERVICES</a><a>LOCATION</a><a>FAQ</a><a>CONTACT</a></nav>
    <div class="call">
      <span class="call__icon"><svg width="14" height="14" viewBox="0 0 24 24"><path fill="#4a8a38" d="M6.6 10.8c1.4 2.8 3.8 5.1 6.6 6.6l2.2-2.2c.3-.3.7-.4 1-.2 1.1.4 2.3.6 3.6.6.6 0 1 .4 1 1V20c0 .6-.4 1-1 1C10.6 21 3 13.4 3 4c0-.6.4-1 1-1h3.5c.6 0 1 .4 1 1 0 1.3.2 2.5.6 3.6.1.3 0 .7-.2 1z"/></svg></span>
      <div><div class="call__label">CALL ME:</div><div class="call__number">617-555-0148</div></div>
    </div>
  </header>
  <div class="hero">
    <div class="hero__people" role="img" aria-label="Photo of a smiling family playing together on a beach at sunset"></div>
    <svg class="hero__curve" width="833" height="400" viewBox="0 0 833 400"><path d="M0 275 Q416 510 833 272 L833 400 L0 400Z" fill="#fff"/><path d="M0 275 Q416 510 833 272" fill="none" stroke="#4a8a38" stroke-width="4"/></svg>
  </div>
  <div class="hero__dots"><span></span><span class="is-on"></span><span></span><span></span></div>
  <div class="hero__title"><h1>Dolores Quintana</h1><p>Attorney At Law</p></div>
  <span class="rule hero__rule"></span>
  <p class="hero__text">Dolores Quintana is a Solo Practitioner focusing her practice on matters pertaining to family law and estate planning.</p>
  <div class="btn hero__btn">REQUEST A FREE CONSULTATION</div>
  <div class="badge">dq</div>

  <div class="portrait"><div class="portrait__photo" role="img" aria-label="Black and white portrait photo of the attorney"></div></div>
  <div class="name-tag"><span class="name-tag__icon"><svg width="10" height="10" viewBox="0 0 10 10"><circle cx="5" cy="3" r="2.2" fill="#fff"/><path d="M1 10c0-2.5 1.8-4 4-4s4 1.5 4 4z" fill="#fff"/></svg></span>Dolores Quintana</div>
  <h2 class="section-title about__title">About <span>Me</span></h2>
  <span class="rule about__rule"></span>
  <div class="about__text">
    <p>Dolores Quintana is a Solo Practitioner focusing her practice on matters pertaining to family law and estate planning.</p>
    <p>When I am retained, my clients are my priority. As a result, I work closely with each one to keep them informed through each step of the legal proceeding. Clients have always expressed to me how frustrating it is when attorneys don't return phone calls. I understand this, as I am often met with the same challenges in the profession. I am proud of my practice and my reputation, and I return calls promptly.</p>
  </div>
  <div class="btn about__btn">LEARN MORE</div>

  <h2 class="section-title centered practice__title">Practice <span>Areas</span></h2>
  <span class="rule practice__rule"></span>
  <div class="card card--family">Family Law</div>
  <div class="card card--estate">Estate Planning</div>

  <section class="contact">
    <h2 class="section-title centered contact__title">Get In <span>Touch</span></h2>
    <span class="rule contact__rule"></span>
    <div class="field" style="left:114px;top:107px;width:196px;height:34px">Full Name</div>
    <div class="field" style="left:318px;top:107px;width:196px;height:34px">Phone</div>
    <div class="field" style="left:521px;top:107px;width:196px;height:34px">Email Address</div>
    <div class="field" style="left:114px;top:151px;width:603px;height:64px">Message</div>
    <div class="btn contact__btn">SEND MESSAGE</div>
  </section>

  <footer class="footer">
    <div class="footer__brand"><span class="brand__mark"></span><div class="brand__name">Dolores Quintana<br>Attorney at Law</div></div>
    <div class="footer__col" style="left:304px"><h3>NAVIGATION</h3><ul><li>HOME</li><li>About Me</li><li>Services</li><li>Location</li><li>Contact Me</li></ul></div>
    <div class="footer__col" style="left:428px"><h3>QUICK LINKS</h3><ul><li>FAQ</li><li>Privacy Policy</li><li>Terms &amp; Conditions</li><li>Disclaimer</li></ul></div>
    <div class="footer__col" style="left:574px"><h3>CONTACT US</h3></div>
    <div class="footer__contact" style="top:88px"><span class="icon-circle"><svg width="9" height="11" viewBox="0 0 9 11"><path d="M4.5 0C2 0 0 2 0 4.4 0 7.5 4.5 11 4.5 11S9 7.5 9 4.4C9 2 7 0 4.5 0z" fill="#4a8a38"/><circle cx="4.5" cy="4.3" r="1.5" fill="#fff"/></svg></span><div>42 Harbor Lane Salem,<br>MA 01970</div></div>
    <div class="footer__contact" style="top:138px"><span class="icon-circle"><svg width="11" height="11" viewBox="0 0 24 24"><path fill="#4a8a38" d="M6.6 10.8c1.4 2.8 3.8 5.1 6.6 6.6l2.2-2.2c.3-.3.7-.4 1-.2 1.1.4 2.3.6 3.6.6.6 0 1 .4 1 1V20c0 .6-.4 1-1 1C10.6 21 3 13.4 3 4c0-.6.4-1 1-1h3.5c.6 0 1 .4 1 1 0 1.3.2 2.5.6 3.6.1.3 0 .7-.2 1z"/></svg></span><div><b>Call Me:</b><br>617-555-0148</div></div>
    <div class="footer__contact" style="top:188px"><span class="icon-circle"><svg width="11" height="8" viewBox="0 0 11 8"><rect width="11" height="8" rx="1" fill="#4a8a38"/><path d="M0.5 0.8 5.5 4.5 10.5 0.8" stroke="#fff" fill="none"/></svg></span><div><b>Email Me:</b><br>dolores.quintana@example.com</div></div>
    <div class="footer__divider"></div>
    <div class="footer__copy">© 2025 &nbsp;/&nbsp; All Rights Reserved</div>
    <div class="social"><span></span><span class="is-hover"></span><span></span></div>
  </footer>
</section>

</div>
</body>
</html>
```